Pepper & Palm Business Card FUN & EXCITING

Here is the Information for the Card:
Jaswinder Bains (Ravi)
E: RaviBains@postlark.com
C: (480) 555-0147
www.PepperPalmLV.com

We don't want traditional Indian cliche, We a playful bold and fun business card.

Files: https://files.cloudvessel.net/share/folders/7TqRmXpZ2vKa9LwBn4YcHd3JsEf6UoGi?usp=share_link

https://files.cloudvessel.net/share/folders/4MzXaQ8rTw2YbNcVk6PsLe5GhJdR3FoU?usp=share_link

Target Market(s)

Las Vegas Local Restaurant

Industry/Entity Type

Indian Restaurant

Contact Information for Business Card

Name, Email, Cell Phone, Company Logo

```html
<!DOCTYPE html>
<html lang="en">
<head>
<meta charset="utf-8">
<title>Pepper &amp; Palm – Business Card</title>
<link href="https://fonts.googleapis.com/css2?family=Montserrat:wght@400;500;700;800&display=swap" rel="stylesheet">
<style>
  :root {
    --page-bg: #2b2b2b;
    --card-bg: #1c1c1c;
    --ink: #ffffff;
    --ink-soft: #d9d9d9;
    --accent: #f07a22;
    --art-cream: #efe6cc;
    --art-orange: #e8812f;
    --art-pink: #e66a8e;
  }
  * { box-sizing: border-box; margin: 0; padding: 0; }
  html, body { width: 1200px; height: 1108px; overflow: hidden; }
  body {
    background: var(--page-bg);
    font-family: "Montserrat", Arial, sans-serif;
    color: var(--ink);
    position: relative;
  }
  .card {
    position: absolute;
    left: 258px;
    width: 695px;
    height: 425px;
    background: var(--card-bg);
    border-radius: 22px;
  }
  .card--front { top: 128px; }
  .card--back { top: 594px; }

  .brand {
    position: absolute;
    display: flex;
    flex-direction: column;
    align-items: center;
    text-align: center;
  }
  .brand__name {
    font-weight: 800;
    color: var(--ink);
    line-height: 1;
    letter-spacing: -0.5px;
  }
  .brand__place {
    font-weight: 700;
    color: var(--ink);
    align-self: flex-end;
  }
  .brand__art {
    background: radial-gradient(ellipse at 50% 45%, var(--art-cream) 0%, #c9b98f 35%, var(--art-orange) 60%, var(--card-bg) 78%);
    border-radius: 12px;
  }
  .brand__tagline {
    color: var(--ink-soft);
    font-weight: 500;
  }

  .card--front .brand { left: 240px; top: 98px; width: 230px; }
  .card--front .brand__name { font-size: 40px; }
  .card--front .brand__place { font-size: 13px; margin-top: 6px; }
  .card--front .brand__art { width: 220px; height: 140px; margin-top: 8px; }
  .card--front .brand__tagline { font-size: 10px; margin-top: 10px; }

  .card--back .brand { left: 90px; top: 146px; width: 170px; }
  .card--back .brand__name { font-size: 29px; }
  .card--back .brand__place { font-size: 10px; margin-top: 5px; }
  .card--back .brand__art { width: 160px; height: 104px; margin-top: 6px; }
  .card--back .brand__tagline { font-size: 8px; margin-top: 8px; }

  .divider {
    position: absolute;
    left: 318px;
    top: 140px;
    width: 2px;
    height: 198px;
    background: var(--accent);
  }
  .contact {
    position: absolute;
    left: 335px;
    top: 138px;
  }
  .contact__name {
    font-size: 27px;
    font-weight: 700;
    color: var(--accent);
    line-height: 1.1;
  }
  .contact__role {
    font-size: 16px;
    color: var(--ink-soft);
    line-height: 1;
  }
  .contact__list {
    list-style: none;
    margin-top: 24px;
  }
  .contact__item {
    display: flex;
    align-items: center;
    gap: 11px;
    font-size: 16px;
    height: 26px;
  }
  .contact__icon { width: 15px; height: 15px; flex: none; }
  .contact__address {
    font-style: normal;
    font-size: 16px;
    line-height: 20px;
    margin-top: 10px;
  }
</style>
</head>
<body>

<section class="card card--front">
  <div class="brand">
    <div class="brand__name">Pepper &amp; Palm</div>
    <div class="brand__place">Las Vegas, NV</div>
    <div class="brand__art" role="img" aria-label="Cartoon illustration of a curry bowl and a naan walking together, with hearts and sparkles"></div>
    <div class="brand__tagline">“A match made in heaven”</div>
  </div>
</section>

<section class="card card--back">
  <div class="brand">
    <div class="brand__name">Pepper &amp; Palm</div>
    <div class="brand__place">Las Vegas, NV</div>
    <div class="brand__art" role="img" aria-label="Cartoon illustration of a curry bowl and a naan walking together, with hearts and sparkles"></div>
    <div class="brand__tagline">“A match made in heaven”</div>
  </div>

  <div class="divider"></div>

  <div class="contact">
    <h1 class="contact__name">Jaswinder Bains (Ravi)</h1>
    <p class="contact__role">owner</p>
    <ul class="contact__list">
      <li class="contact__item">
        <svg class="contact__icon" viewBox="0 0 16 16"><path fill="var(--accent)" d="M1 6c0-2 3-4 7-4s7 2 7 4v1h-4V5H5v2H1zM4 8h8l2 6H2z"/><circle cx="8" cy="11" r="1.6" fill="var(--card-bg)"/></svg>
        <span>(480) 555-0147</span>
      </li>
      <li class="contact__item">
        <svg class="contact__icon" viewBox="0 0 16 16"><rect x="1" y="3" width="14" height="10" rx="1" fill="var(--accent)"/><path d="M1.5 4l6.5 5 6.5-5" fill="none" stroke="var(--card-bg)" stroke-width="1.3"/></svg>
        <span>RaviBains@postlark.com</span>
      </li>
      <li class="contact__item">
        <svg class="contact__icon" viewBox="0 0 16 16"><circle cx="8" cy="8" r="7" fill="var(--accent)"/><path d="M4 5c2 0 2 2 3 3s-1 3 0 5M10 2c-1 2 1 3 2 3s1 3-1 4" fill="none" stroke="var(--card-bg)" stroke-width="1.3"/></svg>
        <span>www.PepperPalmLV.com</span>
      </li>
    </ul>
    <address class="contact__address">418 Larkmoor Ave, #112<br>Fenwick, OH 43190</address>
  </div>
</section>

</body>
</html>
```